Website for software company "velora"

We need a website for our software company/startup named "velora". We are developing several products (currently 3 standard-software products) which are all in different sectors, but all our products are available for Laptops/PC/Mobile Phones/Tablets, ... We do also create custom software and support our customers with consulting to optimize their processes.
We already have a Logo which you can find in the attached files.
We are a young team of 4 members (two founders and 2 employees).

To get an idea of our products -> the first one is a planning software for healthcare organizations (eg. BlueHaven, firebrigade, pharmacy), the second one is a booking software for sport clubs and the third one is a competition software for sports hunting. You see very diverse. Include or ignore this info of our products as you like.

The design has to be a bootstrap 4 (or higher) design. We have licenced FontAwesome as iconset. Responsive design should come without saying.

• Starting page, product pages, news section, contact, team, services

```html
<!DOCTYPE html>
<html lang="en">
<head>
<meta charset="utf-8">
<title>velora — Planning software for healthcare organizations</title>
<link href="https://fonts.googleapis.com/css2?family=Poppins:wght@400;500;600;700&display=swap" rel="stylesheet">
<style>
:root{
  --ink:#232b38;
  --orange:#f5812f;
  --white:#ffffff;
  --text:#555b66;
  --muted:#7a808a;
  --panel:#f4f4f4;
  --line:#d9dce0;
}
*{box-sizing:border-box;margin:0;padding:0}
html,body{width:1200px;height:3439px;overflow:hidden}
body{position:relative;font-family:'Poppins',sans-serif;color:var(--ink);background:var(--white)}
.abs{position:absolute}
a{color:inherit;text-decoration:none}

.hero{left:0;top:0;width:1200px;height:772px;background:var(--ink)}
.brand{font-weight:600;letter-spacing:1px;color:var(--white);display:flex;align-items:center;gap:10px}
.brand .mark{width:14px;height:14px;background:var(--orange)}
.site-logo{left:88px;top:28px;font-size:40px}
.nav{left:434px;top:38px;display:flex;gap:30px;font-size:13px;font-weight:600;color:var(--white);align-items:center}
.nav .active{color:var(--orange)}
.btn-login{left:1011px;top:29px;width:100px;height:40px;border:2px solid var(--white);border-radius:3px;color:var(--white);font-size:13px;font-weight:600;display:flex;align-items:center;justify-content:center}
.hero-title{left:88px;top:262px;width:580px;font-size:45px;line-height:50px;font-weight:700;color:var(--white);white-space:nowrap}
.hero-text{left:88px;top:424px;width:520px;font-size:14px;line-height:23px;color:#e7e9ec}
.btn{display:flex;align-items:center;justify-content:center;gap:8px;font-weight:700;font-size:16px;border-radius:2px}
.btn-orange{background:var(--orange);color:var(--white);box-shadow:0 8px 18px rgba(245,129,47,.35)}
.btn-outline{border:1px solid var(--white);color:var(--white)}
.btn-dark{background:var(--ink);color:var(--white)}
.hero-shot{left:649px;top:223px;width:551px;height:389px;background:var(--white);border-radius:8px 0 0 8px;overflow:hidden}
.hero-shot .fill{position:absolute;left:0;top:0;width:100%;height:100%;background:linear-gradient(90deg,#fafbfc 0 12%,#f1f3f5 12% 27%,#8c9097 27% 57%,#b7bbc0 57% 100%)}
.mouse{left:590px;top:674px}

.forms-shot{left:87px;top:922px;width:512px;height:383px;background:linear-gradient(135deg,#dfe3ea,#cfd5de)}
.section-title{font-size:33px;line-height:40px;font-weight:700}
.forms-title{left:652px;top:1005px;width:460px}
.forms-text{left:654px;top:1137px;width:460px;font-size:15px;line-height:26px;color:var(--text)}

.features{left:89px;top:1413px;width:1027px;height:604px;background:var(--panel)}
.features-title{left:0;top:1505px;width:1200px;text-align:center}
.card{width:180px;height:142px;background:var(--white);display:flex;flex-direction:column;align-items:center;justify-content:flex-end;padding-bottom:20px;gap:10px;font-size:12.5px;font-weight:500;text-align:center;line-height:17px;box-shadow:0 4px 12px rgba(0,0,0,.04)}
.card svg{width:48px;height:48px;fill:none;stroke:var(--ink);stroke-width:1.6;stroke-linecap:round;stroke-linejoin:round}
.card svg .acc{stroke:var(--orange)}

.cta-title{left:0;top:2146px;width:1200px;text-align:center;font-size:42px;line-height:46px;font-weight:700}
.cta-text{left:0;top:2253px;width:1200px;text-align:center;font-size:19px;line-height:29px;color:var(--muted);font-weight:500}

.contact-band{left:0;top:2978px;width:1200px;height:461px;background:var(--panel)}
.quote-card{left:127px;top:2502px;width:475px;height:480px;background:var(--ink);border-radius:10px}
.quote-title{left:207px;top:2644px;width:340px;font-size:32px;line-height:39px;font-weight:700;color:var(--white)}
.quote-text{left:207px;top:2770px;width:320px;font-size:15px;line-height:25px;color:#e3e5e9}
.form-card{left:602px;top:2533px;width:475px;height:480px;background:var(--white);border-radius:0 10px 10px 0;box-shadow:0 10px 40px rgba(0,0,0,.06)}
.field{left:662px;width:357px;height:52px;border-bottom:1.5px solid var(--line);font-size:16px;font-weight:500;padding:0 0 14px 17px;display:flex;align-items:flex-end}
.btn-submit{left:662px;top:2895px;width:156px;height:42px;font-size:14px}

.footer-logo{left:137px;top:3206px;font-size:46px}
.footer-logo.brand{color:var(--ink)}
.f-col h4{font-size:19px;font-weight:700;margin-bottom:8px}
.f-col li{list-style:none;font-size:13px;line-height:23px;color:var(--text)}
.contact-line{display:flex;align-items:center;gap:7px}
.contact-line svg{width:11px;height:11px;fill:var(--orange)}
.socials{display:flex;gap:8px;margin-top:12px}
.socials span{width:24px;height:24px;border-radius:50%;background:var(--white);box-shadow:0 2px 8px rgba(0,0,0,.1);display:flex;align-items:center;justify-content:center}
.socials span i{width:5px;height:5px;border-radius:50%;background:var(--ink)}
.divider{left:89px;top:3355px;width:1022px;height:1px;background:var(--line)}
.copyright{left:0;top:3402px;width:1200px;text-align:center;font-size:13px;color:var(--text)}
.copyright b{color:var(--orange);font-weight:400}
.to-top{left:1111px;top:3369px;width:40px;height:40px;border-radius:50%;background:var(--orange);display:flex;align-items:center;justify-content:center}
</style>
</head>
<body>

<header class="abs hero"></header>
<svg class="abs" style="left:0;top:540px" width="270" height="440" viewBox="0 0 270 440">
  <polygon points="0,20 250,232 0,232" fill="#ffffff"/>
  <polygon points="0,45 233,232 0,418" fill="#f5812f"/>
</svg>

<a class="abs brand site-logo" href="#"><span class="mark"></span>velora</a>
<nav class="abs nav">
  <svg width="13" height="13" viewBox="0 0 16 16"><path d="M8 1 1 7h2v7h4V10h2v4h4V7h2z" fill="#f5812f"/></svg>
  <a href="#">ABOUT US</a><a href="#">SERVICES</a><a class="active" href="#">PRODUCT</a><a href="#">NEWS</a><a href="#">TEAM</a><a href="#">CONTACT</a>
</nav>
<a class="abs btn-login" href="#">LOGIN</a>

<h1 class="abs hero-title">Planning<br>software for healthcare<br>organizations</h1>
<p class="abs hero-text">Nulla quis feugiat mi. Mauris tincidunt dui massa, non feugiat ex blandit vel Nam lacinia dapibus nisi, ac convallis est tempor ac.</p>
<a class="abs btn btn-orange" style="left:88px;top:485px;width:145px;height:47px" href="#">GET NOW <span>→</span></a>
<a class="abs btn btn-outline" style="left:243px;top:485px;width:171px;height:47px" href="#">VIEW DEMO <span>→</span></a>

<div class="abs hero-shot"><div class="fill" role="img" aria-label="App screen showing a hip X-ray planning case with tools panel and patient details"></div></div>
<svg class="abs mouse" width="20" height="32" viewBox="0 0 20 32"><rect x="1.5" y="1.5" width="17" height="29" rx="8.5" fill="none" stroke="#fff" stroke-width="2"/><line x1="10" y1="8" x2="10" y2="13" stroke="#fff" stroke-width="2" stroke-linecap="round"/></svg>

<div class="abs forms-shot" role="img" aria-label="Two overlapping app windows showing the schedule view and the hip X-ray planning view"></div>
<h2 class="abs section-title forms-title">Design Unlimited Forms With the Amazing Drag and Drop Builder</h2>
<p class="abs forms-text">Sed ut perspiciatis unde omnis iste natus error voluptatem<br>accusantium doloremque laudantium, totam rem aperiam,<br>eaque ipsa quae ainventore veritatis et quasi architecto<br>beatae vitae dicta sunt explicabo. Ne.</p>

<section class="abs features"></section>
<h2 class="abs section-title features-title">Most Prominent Features</h2>

<div class="abs card" style="left:226px;top:1566px"><svg viewBox="0 0 48 48"><rect x="6" y="6" width="30" height="26" rx="2"/><line x1="6" y1="12" x2="36" y2="12"/><rect class="acc" x="14" y="18" width="22" height="14" stroke-dasharray="3 2"/><path d="M32 28l8 12 2-5 5-1z"/></svg>Drag &amp; Drop<br>Form Builder</div>
<div class="abs card" style="left:415px;top:1566px"><svg viewBox="0 0 48 48"><rect x="6" y="9" width="36" height="32" rx="3"/><line x1="14" y1="5" x2="14" y2="13"/><line x1="34" y1="5" x2="34" y2="13"/><line class="acc" x1="24" y1="19" x2="24" y2="29"/><circle class="acc" cx="24" cy="34" r=".8"/></svg>Limit and<br>Schedule</div>
<div class="abs card" style="left:604px;top:1566px"><svg viewBox="0 0 48 48"><circle cx="24" cy="24" r="15"/><circle class="acc" cx="24" cy="24" r="6"/><line x1="24" y1="3" x2="24" y2="12"/><line x1="24" y1="36" x2="24" y2="45"/><line x1="3" y1="24" x2="12" y2="24"/><line x1="36" y1="24" x2="45" y2="24"/></svg>CAPTCHA<br>Support</div>
<div class="abs card" style="left:794px;top:1566px"><svg viewBox="0 0 48 48"><path d="M12 4h18l8 8v32H12z"/><path d="M30 4v8h8"/><path class="acc" d="M25 34V20m-6 6 6-6 6 6"/></svg>File Upload</div>
<div class="abs card" style="left:226px;top:1720px"><svg viewBox="0 0 48 48"><rect x="12" y="4" width="24" height="34"/><line class="acc" x1="17" y1="12" x2="31" y2="12"/><line class="acc" x1="17" y1="18" x2="31" y2="18"/><line class="acc" x1="17" y1="24" x2="31" y2="24"/><path d="M4 38h40v6H4z"/></svg>Data Entry<br>Management</div>
<div class="abs card" style="left:415px;top:1720px"><svg viewBox="0 0 48 48"><rect x="13" y="4" width="22" height="40" rx="3"/><circle class="acc" cx="24" cy="20" r="6"/><path class="acc" d="m21 20 2 2 4-4"/><line x1="19" y1="34" x2="29" y2="34"/></svg>Custom Form<br>Field Validations</div>
<div class="abs card" style="left:604px;top:1720px"><svg viewBox="0 0 48 48"><path d="M40 8C28 8 18 18 14 30l4 4C30 30 40 20 40 8z"/><circle class="acc" cx="30" cy="18" r="4"/><path d="M14 30l-6 2 4-8m10 14-2 6 8-4"/><path class="acc" d="M10 38l-4 4"/></svg>Fully Optimized<br>for Page Speed</div>
<div class="abs card" style="left:794px;top:1720px"><svg viewBox="0 0 48 48"><rect x="6" y="6" width="14" height="10" rx="5"/><rect x="30" y="4" width="12" height="8"/><rect class="acc" x="18" y="18" width="12" height="14"/><rect x="6" y="34" width="10" height="10"/><rect x="32" y="34" width="10" height="10"/><path d="M13 16v18m23-22v22"/></svg>Server-Side<br>Validation</div>

<a class="abs btn btn-orange" style="left:496px;top:1893px;width:208px;height:41px;font-size:14px" href="#">SEE ALL FEATURES <span style="margin-left:10px">→</span></a>

<h2 class="abs cta-title">Planning software for<br>healthcare organizations</h2>
<p class="abs cta-text">are Fast, Flexible, and 100% Responsive. Create all kinds of Sitecraft<br>forms with the Easiest Drag &amp; Drop form builder in minutes.</p>
<a class="abs btn btn-orange" style="left:438px;top:2333px;width:144px;height:47px;font-size:17px" href="#">GET NOW <span>→</span></a>
<a class="abs btn btn-dark" style="left:591px;top:2333px;width:172px;height:47px;font-size:17px" href="#">VIEW DEMO <span>→</span></a>

<div class="abs contact-band"></div>
<div class="abs quote-card"></div>
<h2 class="abs quote-title">Need a quote<br>for a project ?<br>Get in touch...</h2>
<p class="abs quote-text">If you're ere it means you want to start a journey.We would love to get to know you an take journey.We'll be perfect for each other- you'll see..</p>

<form class="abs form-card"></form>
<div class="abs field" style="top:2609px">Name</div>
<div class="abs field" style="top:2659px">Phone number</div>
<div class="abs field" style="top:2711px">Email</div>
<div class="abs field" style="top:2763px">Subject</div>
<div class="abs field" style="top:2815px">Your Enquiry</div>
<a class="abs btn btn-orange btn-submit" href="#">SUBMIT NOW →</a>

<a class="abs brand footer-logo" href="#"><span class="mark" style="width:18px;height:18px"></span>velora</a>
<div class="abs f-col" style="left:447px;top:3130px"><h4>Useful Links</h4><ul><li>Home</li><li>About Us</li><li>Services</li><li>Product</li><li>News</li><li>Team</li><li>Contact</li></ul></div>
<div class="abs f-col" style="left:628px;top:3130px"><h4>Our Services</h4><ul><li>Software Solutions</li><li>Market Analysis</li><li>Web Development</li><li>Digital Solutions</li><li>Graphics Design</li><li>Consultations</li></ul></div>
<div class="abs f-col" style="left:848px;top:3130px"><h4>Get In Touch</h4><ul>
  <li class="contact-line"><svg viewBox="0 0 12 12"><path d="M6 0a4 4 0 0 0-4 4c0 3 4 8 4 8s4-5 4-8a4 4 0 0 0-4-4zm0 5.5A1.5 1.5 0 1 1 6 2.5a1.5 1.5 0 0 1 0 3z"/></svg>12 Larkfield Road, Northbridge</li>
  <li class="contact-line"><svg viewBox="0 0 12 12"><path d="M0 2h12v8H0z"/></svg>hello@velora-mail.net</li>
  <li class="contact-line"><svg viewBox="0 0 12 12"><path d="M2 0h3l1 3-2 1a7 7 0 0 0 4 4l1-2 3 1v3a2 2 0 0 1-2 2A10 10 0 0 1 0 2a2 2 0 0 1 2-2z"/></svg>Call : +014 (562) 390</li>
</ul>
<div class="socials"><span><i></i></span><span><i></i></span><span><i></i></span><span><i></i></span></div></div>

<div class="abs divider"></div>
<p class="abs copyright">© 2022 <b>velora</b>. All rights reserved</p>
<a class="abs to-top" href="#"><svg width="12" height="8" viewBox="0 0 12 8"><path d="M1 7l5-5 5 5" fill="none" stroke="#fff" stroke-width="2"/></svg></a>

</body>
</html>
```